Webdesign für Steuerberaterin
Zielgruppe
Ich bin Steuerberaterin. Meine Zielgruppe sind sowohl Privatpersonen als auch Unternehmer sowie Männer und Frauen.
Aufgabenstellung
Bitte mein Logo und Foto mit berücksichtigen. Ich möchte keine Website, auf der alle 'Reiter' als eine Seite von oben nach unten durchlaufen. Sondern wirklich einzelne, voneinander getrennte Seiten.

```html
<!DOCTYPE html>
<html lang="de">
<head>
<meta charset="utf-8">
<title>Maren Brodtke – Steuerberaterin</title>
<link href="https://fonts.googleapis.com/css2?family=Crimson+Pro:wght@400&family=Montserrat:wght@400;500&display=swap" rel="stylesheet">
<style>
  :root {
    --stage: #f3eee4;
    --paper: #ffffff;
    --band: #f5f5f5;
    --ink: #1d1d1f;
    --muted: #4a4a4a;
    --gold: #c4922c;
    --line: #e6e6e6;
    --btn-light: #f1f1f1;
    --photo-a: #f4f1f0;
    --photo-b: #1d2233;
  }
  * { box-sizing: border-box; margin: 0; padding: 0; }
  html, body { width: 1200px; height: 948px; overflow: hidden; }
  body { background: var(--stage); position: relative; font-family: "Montserrat", sans-serif; color: var(--ink); }
  .serif { font-family: "Crimson Pro", serif; font-weight: 400; }
  .abs { position: absolute; }

  .screen { position: absolute; background: var(--paper); overflow: hidden; }
  .desktop { left: 36px; top: 104px; width: 880px; height: 740px; }
  .mobile { left: 950px; top: 22px; width: 210px; height: 903px; }

  .brand { font-family: "Crimson Pro", serif; color: var(--gold); line-height: 1; white-space: nowrap; }
  .brand-sub { display: block; font-size: 0.3em; letter-spacing: 0.22em; margin-top: 3px; }
  .mark { border-radius: 50%; background: var(--ink); }

  .nav { top: 16px; display: flex; font-size: 5.6px; letter-spacing: 0.04em; }
  .nav a { color: var(--muted); text-decoration: none; position: absolute; white-space: nowrap; }
  .nav a.active { color: var(--ink); border-bottom: 1px solid var(--gold); padding-bottom: 4px; }

  .hero-title { line-height: 1.08; color: var(--ink); }
  .hero-lead { color: var(--ink); }

  .btn { display: flex; align-items: center; justify-content: space-between; padding: 0 9px; font-size: 5.6px; letter-spacing: 0.04em; }
  .btn svg { width: 5px; height: 5px; }
  .btn-light { background: var(--btn-light); color: var(--ink); }
  .btn-dark { background: var(--ink); color: #fff; }

  .portrait { background: linear-gradient(180deg, var(--photo-a) 0%, #d9c4b8 30%, var(--photo-b) 62%, var(--photo-b) 100%); }

  .band { background: var(--band); left: 0; right: 0; }
  .section-title { line-height: 1.05; color: var(--ink); }
  .copy p { color: var(--muted); margin-bottom: 1.2em; }

  .foot-col h4 { font-family: "Crimson Pro", serif; font-weight: 400; color: var(--ink); margin-bottom: 4px; }
  .foot-col a { display: block; color: var(--ink); text-decoration: none; }
  .copyright { color: var(--ink); white-space: nowrap; }
</style>
</head>
<body>

<main class="screen desktop">
  <header>
    <div class="abs brand" style="left:37px; top:12px; font-size:19px;">Maren Brodtke<span class="brand-sub" style="color:var(--ink);">STEUERBERATERIN</span></div>
    <nav class="abs nav" style="left:0; right:0;">
      <a class="active" href="#" style="left:647px;">START</a>
      <a href="#" style="left:693px;">ÜBER MICH</a>
      <a href="#" style="left:753px;">LEISTUNGEN</a>
      <a href="#" style="left:813px;">KONTAKT</a>
    </nav>
  </header>

  <section class="hero">
    <div class="abs mark" style="left:156px; top:143px; width:16px; height:16px;"></div>
    <h1 class="abs serif hero-title" style="left:156px; top:177px; font-size:22px;">Schön,<br>dass Sie da sind!</h1>
    <p class="abs hero-lead" style="left:156px; top:231px; font-size:6.8px;">Ich freue mich, dass Sie den Weg zu mir gefunden haben!</p>
    <a class="abs btn btn-light" style="left:156px; top:260px; width:91px; height:25px;">ÜBER MICH
      <svg viewBox="0 0 10 10"><path d="M3 1l4 4-4 4" fill="none" stroke="currentColor" stroke-width="1.4"/></svg></a>
    <a class="abs btn btn-dark" style="left:257px; top:260px; width:91px; height:25px;">LEISTUNGEN
      <svg viewBox="0 0 10 10"><path d="M3 1l4 4-4 4" fill="none" stroke="currentColor" stroke-width="1.4"/></svg></a>
    <div class="abs portrait" role="img" aria-label="Porträtfoto der Steuerberaterin im dunklen Blazer mit verschränkten Armen" style="left:526px; top:115px; width:241px; height:314px;"></div>
  </section>

  <section class="abs band" style="top:429px; height:211px;">
    <h2 class="abs serif section-title" style="left:156px; top:52px; font-size:14px;">Sie sind bei mir<br>genau richtig.</h2>
    <div class="abs copy" style="left:270px; top:55px; width:210px; font-size:5.6px; line-height:1.3;">
      <p>Egal, ob Sie Privatperson sind, die Ihre Einkommensteuer-Erklärung in vertrauensvolle Hände geben möchte, oder Unternehmer, der sich z.B. das „Rundum-Sorglos-Paket“ mit Buchführung, Jahresabschluss und Steuererklärungen wünscht.</p>
      <p>Schauen Sie sich hier gerne um und melden Sie sich bei mir – ich bin bei jedem steuerlichen Thema gerne Ihr kompetenter und zuverlässiger Ansprechpartner.</p>
      <p>Für mich ist es eine Selbstverständlichkeit, dass ich auch nach mehr als 12 Jahren Berufserfahrung durch permanente Fortbildungen immer auf dem aktuellsten Stand der relevanten Gesetze und Verordnungen bin. Nur so kann ich Sie bestmöglich beraten.</p>
    </div>
  </section>
  <div class="abs" style="left:252px; top:413px; width:1px; height:33px; background:var(--muted);"></div>

  <footer class="abs" style="left:0; right:0; top:640px; height:100px; border-top:1px solid var(--line);">
    <div class="abs mark" style="left:166px; top:22px; width:14px; height:14px;"></div>
    <div class="abs brand" style="left:156px; top:40px; font-size:10px;">Maren Brodtke</div>
    <p class="abs copyright" style="left:156px; top:70px; font-size:5.6px;">© 2021 — Maren Brodtke Steuerberaterin</p>
    <div class="abs foot-col" style="left:585px; top:22px; font-size:5.6px; line-height:1.9;">
      <h4 style="font-size:6.4px;">Navigation</h4>
      <a href="#">Start</a><a href="#">Über mich</a><a href="#">Leistungen</a><a href="#">Kontakt</a>
    </div>
    <div class="abs foot-col" style="left:662px; top:22px; font-size:5.6px; line-height:1.9;">
      <h4 style="font-size:6.4px;">Rechtliches</h4>
      <a href="#">Datenschutzerklärung</a><a href="#">AGB</a><a href="#">Impressum</a>
    </div>
  </footer>
</main>

<main class="screen mobile">
  <header>
    <div class="abs brand" style="left:12px; top:10px; font-size:14px;">Maren Brodtke<span class="brand-sub" style="color:var(--ink);">STEUERBERATERIN</span></div>
    <svg class="abs" style="left:183px; top:20px; width:14px; height:6px;" viewBox="0 0 14 6"><path d="M0 1h14M5 5h9" stroke="var(--ink)" stroke-width="1"/></svg>
  </header>

  <section class="hero">
    <div class="abs mark" style="left:12px; top:62px; width:16px; height:16px;"></div>
    <h1 class="abs serif hero-title" style="left:12px; top:98px; font-size:22px;">Schön,<br>dass sie da sind!</h1>
    <p class="abs hero-lead" style="left:12px; top:154px; width:135px; font-size:6.8px; line-height:1.3;">Ich freue mich, dass Sie den Weg zu mir gefunden haben!</p>
    <div class="abs portrait" role="img" aria-label="Porträtfoto der Steuerberaterin im dunklen Blazer mit verschränkten Armen" style="left:73px; top:178px; width:137px; height:166px;"></div>
  </section>

  <section class="abs band" style="top:344px; height:338px;">
    <a class="abs btn btn-light" style="left:12px; top:22px; width:89px; height:30px; background:#fff;">ÜBER MICH
      <svg viewBox="0 0 10 10"><path d="M3 1l4 4-4 4" fill="none" stroke="currentColor" stroke-width="1.4"/></svg></a>
    <a class="abs btn btn-dark" style="left:108px; top:22px; width:90px; height:30px;">LEISTUNGEN
      <svg viewBox="0 0 10 10"><path d="M3 1l4 4-4 4" fill="none" stroke="currentColor" stroke-width="1.4"/></svg></a>
    <h2 class="abs serif section-title" style="left:12px; top:73px; font-size:17px;">Sie sind bei mir<br>genau richtig.</h2>
    <div class="abs copy" style="left:12px; top:127px; width:168px; font-size:6.4px; line-height:1.3;">
      <p>Egal, ob Sie Privatperson sind, die Ihre Einkommensteuer-Erklärung in vertrauensvolle Hände geben möchte, oder Unternehmer, der sich z.B. das „Rundum-Sorglos-Paket“ mit Buchführung, Jahresabschluss und Steuererklärungen wünscht.</p>
      <p>Schauen Sie sich hier gerne um und melden Sie sich bei mir – ich bin bei jedem steuerlichen Thema gerne Ihr kompetenter und zuverlässiger Ansprechpartner.</p>
      <p>Für mich ist es eine Selbstverständlichkeit, dass ich auch nach mehr als 12 Jahren Berufserfahrung durch permanente Fortbildungen immer auf dem aktuellsten Stand der relevanten Gesetze und Verordnungen bin. Nur so kann ich Sie bestmöglich beraten.</p>
    </div>
  </section>

  <footer class="abs" style="left:0; right:0; top:682px; height:221px;">
    <div class="abs mark" style="left:22px; top:22px; width:14px; height:14px;"></div>
    <div class="abs brand" style="left:12px; top:41px; font-size:10px;">Maren Brodtke</div>
    <p class="abs copyright" style="left:12px; top:80px; font-size:6.2px;">© 2021 — Maren Brodtke Steuerberaterin</p>
    <div class="abs foot-col" style="left:12px; top:104px; font-size:6.2px; line-height:2.1;">
      <h4 style="font-size:7px;">Navigation</h4>
      <a href="#">Start</a><a href="#">Über mich</a><a href="#">Leistungen</a><a href="#">Kontakt</a>
    </div>
    <div class="abs foot-col" style="left:106px; top:104px; font-size:6.2px; line-height:2.1;">
      <h4 style="font-size:7px;">Rechtliches</h4>
      <a href="#">Datenschutzerklärung</a><a href="#">AGB</a><a href="#">Impressum</a>
    </div>
  </footer>
</main>

</body>
</html>
```